Simple Business Card Design for Tavlo

Job:

Make a very simple, minimalist business card design with my details including adjusted logo. One side to be white (with logo & text). Other side to be yellow - try plain or with logo (or part of logo eg Z). Need business card to have continuity with website.

Logo:
Our logo is made from a free download font website:
http://www.typewell.net/search.php?q=rubber
but the spacing/kerning needs correcting/adjusting as the font spaces unevenly between letters (see attached files). Need logo to be very crisp/sharp when printed.

Printing:
We will be using Plika.com so the design needs to conform to their requirements, see here:

http://uk.plika.com/products/luxe/business-cards.html (scroll down for dimensions and guidelines)

Design:

must say "plant-based food consulting" underneath logo or somewhere
no address needed in contact section
sharp corners (not rounded)
one side white, one side yellow

name: Rosalind Whitcombe
1xmobile number: +44 7700900463
1xtwiiter: @brimcounsel
website address www.orchardtable.com
email address brim@orchardtable.com

Should be easy quick job, prompt + detailed feedback given, am online in UK 9am-10pm for next 3 days. Website is www.orchardtable.com

Industry/Entity Type

Business

Requirements
Must have
• The logo must be corrected. The kerning is not right.

Please use a warm-grey for text

Please submit in matt format, we will be printing matt finish.

Should not have
• Avoid using banners or curvy highlights

Please avoid using black

Please avoid submitting in gloss finish

```html
<!DOCTYPE html>
<html lang="en">
<head>
<meta charset="utf-8">
<title>Brim business card – front and back</title>
<link rel="stylesheet" href="https://fonts.googleapis.com/css2?family=Cinzel:wght@400;700&display=swap">
<style>
  :root {
    --backdrop: #6f6f6f;
    --card-front: #ffffff;
    --card-back: #f9ef63;
    --accent: #f5e64a;
    --warm-grey: #6b645c;
    --warm-grey-light: #8a8279;
    --rule: #cfc9c1;
  }
  * { margin: 0; padding: 0; box-sizing: border-box; }
  html, body {
    width: 1200px;
    height: 750px;
    overflow: hidden;
    background: var(--backdrop);
  }
  .canvas {
    position: relative;
    width: 1200px;
    height: 750px;
    font-family: "Cinzel", serif;
  }
  .card {
    position: absolute;
    top: 210px;
    width: 524px;
    height: 300px;
    overflow: hidden;
  }
  .card--front { left: 61px; background: var(--card-front); }
  .card--back { left: 612px; background: var(--card-back); }

  .brand {
    position: absolute;
    color: var(--warm-grey);
    white-space: nowrap;
  }
  .card--front .brand {
    left: 44px;
    top: 112px;
    width: 200px;
    text-align: center;
  }
  .card--back .brand {
    left: 0;
    right: 0;
    top: 102px;
    text-align: center;
  }
  .wordmark {
    font-weight: 700;
    line-height: 1;
    letter-spacing: 4px;
  }
  .card--front .wordmark { font-size: 60px; }
  .card--back .wordmark { font-size: 84px; }
  .tagline {
    font-weight: 400;
    letter-spacing: 1px;
    color: var(--warm-grey-light);
  }
  .card--front .tagline { font-size: 10px; margin-top: 8px; }
  .card--back .tagline { font-size: 13px; margin-top: 12px; color: var(--warm-grey); }

  .divider {
    position: absolute;
    left: 261px;
    top: 94px;
    width: 2px;
    height: 110px;
    background: linear-gradient(to bottom, rgba(245,230,74,0), var(--accent) 30%, var(--accent) 70%, rgba(245,230,74,0));
  }

  .contact-block {
    position: absolute;
    left: 288px;
    top: 100px;
  }
  .person-name {
    color: var(--warm-grey);
    font-weight: 700;
    font-size: 14px;
    line-height: 18px;
    white-space: nowrap;
  }
  .person-role {
    color: var(--warm-grey-light);
    font-size: 12px;
    line-height: 16px;
    margin-bottom: 10px;
  }
  .contact-list { list-style: none; }
  .contact-item {
    display: flex;
    align-items: center;
    height: 15px;
    color: var(--warm-grey);
    font-size: 11px;
    white-space: nowrap;
  }
  .contact-icon {
    width: 12px;
    height: 10px;
    margin-right: 10px;
    flex: none;
  }

  .base-rule {
    position: absolute;
    left: 0;
    width: 100%;
    top: 275px;
    height: 2px;
    background: var(--rule);
  }
  .base-band {
    position: absolute;
    left: 0;
    width: 100%;
    top: 280px;
    height: 20px;
    background: var(--card-back);
  }
</style>
</head>
<body>
<main class="canvas">
  <section class="card card--front" aria-label="Card front">
    <div class="brand">
      <div class="wordmark">BRIM</div>
      <div class="tagline">plant-based food consulting</div>
    </div>
    <div class="divider"></div>
    <div class="contact-block">
      <p class="person-name">Rosalind Whitcombe</p>
      <p class="person-role">Manager</p>
      <ul class="contact-list">
        <li class="contact-item">
          <svg class="contact-icon" viewBox="0 0 12 10" aria-hidden="true">
            <path d="M1 3.5 C1 1.5 11 1.5 11 3.5 L9 4 L8.3 3 L3.7 3 L3 4 Z" fill="#6b645c"/>
            <path d="M3.5 4.5 L8.5 4.5 L10 9 L2 9 Z" fill="#6b645c"/>
          </svg>
          +44 7700 900463
        </li>
        <li class="contact-item">
          <svg class="contact-icon" viewBox="0 0 12 10" aria-hidden="true">
            <rect x="0.5" y="1" width="11" height="8" fill="#6b645c"/>
            <path d="M0.8 1.3 L6 5.5 L11.2 1.3" fill="none" stroke="#ffffff" stroke-width="1"/>
          </svg>
          brim@orchardtable.com
        </li>
        <li class="contact-item">
          <svg class="contact-icon" viewBox="0 0 12 10" aria-hidden="true">
            <rect x="1" y="0.8" width="10" height="6.5" fill="none" stroke="#6b645c" stroke-width="1.4"/>
            <rect x="4" y="8.2" width="4" height="1.3" fill="#6b645c"/>
          </svg>
          www.orchardtable.com
        </li>
        <li class="contact-item">
          <svg class="contact-icon" viewBox="0 0 12 10" aria-hidden="true">
            <path d="M1 1 H11 V7 H5 L2.5 9.5 V7 H1 Z" fill="#6b645c"/>
          </svg>
          @brimcounsel
        </li>
      </ul>
    </div>
    <div class="base-rule"></div>
    <div class="base-band"></div>
  </section>

  <section class="card card--back" aria-label="Card back">
    <div class="brand">
      <div class="wordmark">BRIM</div>
      <div class="tagline">plant-based food consulting</div>
    </div>
  </section>
</main>
</body>
</html>
```